Etikett für Rotweinflasche
Liebe farbkosmos Atelier, wir werden uns bei der endgültigen Etikettengestaltung (finale Größe + Rückseite) noch an Euch melden. Bitte sendet uns euren Kontakt an helga.brandt@morvelli.wine
Zielgruppe
Morvelli Italia ist ein exklusives Boutique-Weingut in Sizilien, das hochqualitative Spitzenweine in kleinen Mengen mit modernster Technologie und stets nachhaltig erzeugt. Wir hinterfragen sowohl in der Agronomie im Weingarten als auch in der Önologie im Weinkeller alle herrschenden Traditionen und trachten danach, stets das beste Endprodukt zu kreieren. Der vulkanische, kalkreiche Boden Siziliens sowie trockene, sonnenreiche und niederschlagsarme Vegetationsperioden sind unsere optimale Basis.
Zielgruppe: Internationale Genussmenschen jeglichen Alters, die sich bewusst auch höherpreisige Weine (um die €30+) gönnen , vor allem kunstaffine young professionals mit Qualitäts-& Nachhaltigkeitsanspruch
Aufgabenstellung
Das Etikett ist für Rotwein-Flaschen (Cabernet Sauvignon / Nero D'Avola / Frappato / Syrah / Cerasuolo / Petit Verdot / sowie einen Bourdeaux-Cuveè aus Cabernet Sauvignon und Petit Verdot) .
Die Flasche ist reinschwarz, sehr hochwertig und schwer.
Flaschenform: Bordeauxflasche siehe technisches Datenblatt
Sleeve über dem Korken: schwarz mit weißer Schrift wie bisher
Zu gestalten ist das Etikett der Vorderseite. Zumindest die jeweilige Rotwein-Sorte ist auch textlich darzustellen (zwecks Scannen mit Trubel-App)
Der Kreativität kann freien Lauf gelassen werden! Unterscheidbarkeit vom Markt ist explizit gewollt.
Unsere aktuellen Etiketten und Markenauftritt siehe: https://morvelli.wine/shop/

```html
<!DOCTYPE html>
<html lang="it">
<head>
<meta charset="utf-8">
<title>Etichette vino rosso – serie Sicilia</title>
<link rel="stylesheet" href="https://fonts.googleapis.com/css2?family=Cinzel:wght@400;800&display=swap">
<style>
  :root {
    --page: #ffffff;
    --paper: #e2dedb;
    --frame: #ffffff;
    --crimson: #b0003f;
    --ink: #1b1718;
    --bloom-violet: #9a90c0;
    --bloom-leaf: #7fa36a;
    --bloom-sun: #e7c44a;
    --engraving: rgba(234, 223, 220, 0.22);
  }
  * { box-sizing: border-box; margin: 0; padding: 0; }
  html, body {
    width: 882px;
    height: 1200px;
    overflow: hidden;
    background: var(--page);
  }
  .label-series {
    width: 882px;
    height: 1200px;
    display: flex;
    justify-content: center;
    align-items: center;
    gap: 36px;
  }
  .label {
    position: relative;
    width: 250px;
    height: 400px;
    background: var(--paper);
    font-family: "Cinzel", Georgia, serif;
    overflow: hidden;
  }
  .label__title,
  .label__title-inverted {
    position: absolute;
    left: 0;
    right: 0;
    z-index: 3;
    text-align: center;
    font-size: 13px;
    line-height: 16px;
    letter-spacing: 3px;
    white-space: nowrap;
  }
  .label__title {
    top: 52px;
    color: var(--ink);
  }
  .label__title-inverted {
    bottom: 36px;
    color: var(--crimson);
    transform: rotate(180deg);
  }
  .word--strong { font-weight: 800; }
  .word--light { font-weight: 400; }

  .label__frame {
    position: absolute;
    left: 19px;
    top: 133px;
    width: 213px;
    height: 187px;
    background: var(--frame);
  }
  .label__field {
    position: absolute;
    left: 40px;
    top: 153px;
    width: 172px;
    height: 146px;
    background: var(--crimson);
  }
  .label__machine {
    position: absolute;
    left: 40px;
    top: 153px;
    width: 172px;
    height: 146px;
    background: linear-gradient(180deg, rgba(234,223,220,0) 0%, var(--engraving) 45%, var(--engraving) 100%);
  }
  .label__bloom {
    position: absolute;
    z-index: 2;
    border-radius: 40% 40% 8px 8px;
  }
  .label--nero .label__bloom {
    left: 56px; top: 74px; width: 102px; height: 112px;
    background: linear-gradient(180deg, var(--bloom-violet) 0%, var(--bloom-leaf) 100%);
    opacity: 0.75;
  }
  .label--cabernet .label__bloom {
    left: 86px; top: 94px; width: 78px; height: 100px;
    background: linear-gradient(180deg, var(--bloom-sun) 0%, var(--bloom-leaf) 100%);
    opacity: 0.8;
  }
  .label--frappato .label__bloom {
    left: 70px; top: 74px; width: 110px; height: 140px;
    background: linear-gradient(180deg, var(--bloom-leaf) 0%, var(--bloom-violet) 50%, var(--bloom-leaf) 100%);
    opacity: 0.8;
  }
</style>
</head>
<body>
<main class="label-series">

  <article class="label label--nero">
    <h2 class="label__title"><span class="word--strong">NERO</span> <span class="word--light">D'AVOLA</span></h2>
    <div class="label__frame"></div>
    <div class="label__field"></div>
    <div class="label__machine" role="img" aria-label="Engraved vintage typewriter in light line work"></div>
    <div class="label__bloom" role="img" aria-label="Bouquet of violet star-shaped wildflowers rising from the typewriter"></div>
    <p class="label__title-inverted"><span class="word--strong">NERO</span> <span class="word--light">D'AVOLA</span></p>
  </article>

  <article class="label label--cabernet">
    <h2 class="label__title"><span class="word--strong">CABERNET</span><br><span class="word--light">SAUVIGNON</span></h2>
    <div class="label__frame"></div>
    <div class="label__field"></div>
    <div class="label__machine" role="img" aria-label="Engraved antique typewriter with fanned type bars"></div>
    <div class="label__bloom" role="img" aria-label="Yellow daisies growing from the typewriter's type bars"></div>
    <p class="label__title-inverted"><span class="word--strong">CABERNET</span><br><span class="word--light">SAUVIGNON</span></p>
  </article>

  <article class="label label--frappato">
    <h2 class="label__title"><span class="word--strong">FRAPPATO</span></h2>
    <div class="label__frame"></div>
    <div class="label__field"></div>
    <div class="label__machine" role="img" aria-label="Ornate engraved typewriter in light line work"></div>
    <div class="label__bloom" role="img" aria-label="Morning glory vine with lilac blossoms and green leaves entwining the typewriter"></div>
    <p class="label__title-inverted"><span class="word--strong">FRAPPATO</span></p>
  </article>

</main>
</body>
</html>
```